Business Card Design Competition

We need a business card design for our Internet Marketing company. We require both front and back designs and the final card must be 89x53mm in size, plus crop marks to 91x55mm. Colours as per logo, plus perhaps black and/or grey (#828282).
Final text must be editable (if you can supply an editable Fireworks PNG, even better)...
FRONT TEXT:
Full Name
Position
Address Line
Suburb, State, Postcode
Phone: 0000 000 000
Mobile: 0000 000 000
Email: xxx@brightlanemedia.com.au
Web: www.brightlanemedia.com.au
Rear of card should be a fresh design plus our slogan text: "Putting You Forward" in large font, then in small text "Kestrel Holdings Pty Ltd (ABN: 42 561 903 774)".
Target Market(s)
Small/Medium Businesses
Industry/Entity Type
Business

```html
<!DOCTYPE html>
<html lang="en">
<head>
<meta charset="utf-8">
<title>Brightlane Media – Business Card</title>
<link rel="stylesheet" href="https://fonts.googleapis.com/css2?family=Open+Sans:wght@400;600;700&family=Quicksand:wght@400&display=swap">
<style>
  :root {
    --page: #ebe7e2;
    --card: #848484;
    --card-shade: #7c7c7c;
    --ink: #2a2a2a;
    --ink-soft: #333333;
    --brand-green: #8dc63f;
    --brand-orange: #f7941d;
    --deco: rgba(255, 255, 255, 0.07);
  }
  * { margin: 0; padding: 0; box-sizing: border-box; }
  html, body { width: 1200px; height: 900px; overflow: hidden; }
  body {
    background: var(--page);
    position: relative;
    font-family: "Open Sans", Arial, sans-serif;
    color: var(--ink);
  }
  .card {
    position: absolute;
    top: 290px;
    width: 545px;
    height: 313px;
    border-radius: 18px;
    background: linear-gradient(160deg, var(--card) 0%, var(--card-shade) 100%);
    overflow: hidden;
  }
  .card--front { left: 37px; }
  .card--back { left: 620px; }

  .brand-dot {
    position: absolute;
    width: 78px;
    height: 78px;
    border-radius: 50%;
    background: var(--brand-orange);
  }
  .brand-name {
    position: absolute;
    font-weight: 600;
    color: var(--brand-green);
    line-height: 1;
  }
  .brand-name span { display: block; }
  .brand-name .line-1 { font-size: 31px; }
  .brand-name .line-2 { font-size: 22px; margin-top: 3px; }

  .card--front .brand-dot { left: 33px; top: 25px; }
  .card--front .brand-name { left: 124px; top: 35px; }

  .deco-circle {
    position: absolute;
    left: 290px;
    top: 10px;
    width: 300px;
    height: 300px;
    border-radius: 50%;
    background: var(--deco);
  }

  .person-name {
    position: absolute;
    left: 43px; top: 175px;
    font-size: 16px; font-weight: 700;
  }
  .person-role {
    position: absolute;
    left: 43px; top: 195px;
    font-size: 11px;
  }
  .address {
    position: absolute;
    left: 43px; top: 230px;
    font-size: 11px;
  }
  .contact {
    position: absolute;
    display: flex;
    align-items: center;
    gap: 8px;
    font-size: 11px;
    color: var(--ink-soft);
  }
  .contact svg { width: 13px; height: 13px; flex: none; }
  .contact--mobile { left: 43px; top: 257px; }
  .contact--phone { left: 43px; top: 274px; }
  .contact--email { left: 165px; top: 257px; }
  .contact--web { left: 165px; top: 274px; }

  .card--back .brand-dot { left: 145px; top: 95px; }
  .card--back .brand-name { left: 234px; top: 105px; }
  .slogan {
    position: absolute;
    left: 0; right: 0; top: 194px;
    text-align: center;
    font-family: "Quicksand", "Open Sans", sans-serif;
    font-size: 25px;
    letter-spacing: 3px;
    color: var(--ink);
  }
  .legal {
    position: absolute;
    left: 0; right: 32px; top: 283px;
    text-align: center;
    font-size: 10px;
    color: var(--ink-soft);
  }
</style>
</head>
<body>

<section class="card card--front" aria-label="Card front">
  <div class="deco-circle" aria-hidden="true"></div>
  <div class="brand-dot" aria-hidden="true"></div>
  <div class="brand-name"><span class="line-1">Brightlane</span><span class="line-2">Media</span></div>

  <p class="person-name">Liam Carver</p>
  <p class="person-role">Company Director</p>
  <p class="address">18 harbour view road, Millbrook County Down BT30 4QS 1234</p>

  <p class="contact contact--mobile">
    <svg viewBox="0 0 16 16" aria-hidden="true"><rect x="4.5" y="1" width="7" height="14" rx="1.5" fill="#2a2a2a"/><rect x="6" y="3" width="4" height="7" fill="#848484"/></svg>
    061-700-4812
  </p>
  <p class="contact contact--phone">
    <svg viewBox="0 0 16 16" aria-hidden="true"><path d="M2 6c0-2 2-3 6-3s6 1 6 3v1h-3V5.5H5V7H2z" fill="#2a2a2a"/><rect x="3" y="8" width="10" height="6" rx="1" fill="#2a2a2a"/></svg>
    061-700-4890
  </p>
  <p class="contact contact--email">
    <svg viewBox="0 0 16 16" aria-hidden="true"><rect x="1.5" y="3.5" width="13" height="9" fill="none" stroke="#2a2a2a" stroke-width="1.5"/><path d="M1.5 3.5 8 9l6.5-5.5" fill="none" stroke="#2a2a2a" stroke-width="1.5"/></svg>
    liam@brightlanemedia.com.au
  </p>
  <p class="contact contact--web">
    <svg viewBox="0 0 16 16" aria-hidden="true"><circle cx="8" cy="8" r="6.5" fill="none" stroke="#2a2a2a" stroke-width="1.4"/><ellipse cx="8" cy="8" rx="3" ry="6.5" fill="none" stroke="#2a2a2a" stroke-width="1.2"/><path d="M1.5 8h13" stroke="#2a2a2a" stroke-width="1.2"/></svg>
    brightlanemedia.com.au
  </p>
</section>

<section class="card card--back" aria-label="Card back">
  <div class="brand-dot" aria-hidden="true"></div>
  <div class="brand-name"><span class="line-1">Brightlane</span><span class="line-2">Media</span></div>
  <p class="slogan">Putting You Forward</p>
  <p class="legal">Kestrel Holdings Pty Ltd (ABN: 42 561 903 774)</p>
</section>

</body>
</html>
```